Mobile Repair Service on location needs a Web Design

We are starting a new mobile device repair service called Handset Haven and our website needs a design!

Hello Designers!
First, we'd like to make clear this is more than a simple web design contest, we want the designers to create an idea. We want someone who can create the whole theme of the service's we provide. We want someone that can help design our visual branding, help us communicate a sentiment. And we are willing to pay for that.

Who are we?
Our company is based in Rotterdam, the Netherlands. We provide different services for all kinds of electronic devices. The kind of services we provide are, among other things, installations of hardware and software and the repair of broken or malfunctioning devices.
We are starting a new service that offers mobile device repairs on location, be it at the home of our customers, their office, or any other place. Just give us the address and we will come to you for the repair job. This is also our main USP. We have multiple skilled engineers who drive trough the country on a daily basis and can be on location within a working day. Repair is done immediately onsite while the customer waits. At this stage we will start with the smartphone product-group within the mobile devices. In a second phase we might also add tablets.
People don't want to be without their phone for weeks because of some parts that needed to be ordered by a repair center they had to sent their phone to. We offer a fully functional mobile repair center in the form of specially customized vans. These vans have all the tools and utilities needed by our engineers to safely repair your mobile device. Your phone is being repaired directly in front of you, the next business-day, on a location you desire.

For this new service we are creating a website called Handset Haven. The website needs a story and matching design and this is where you come in. We are not looking for a simple template design we can get from any place. We need a story. We want you to create an idea, build a unique theme or vision that helps sell the product/service. This goes beyond the design of the website. We need the whole package, the design you are creating needs to have returning elements like icons, color use, images, maybe even characters etc. You name it! There needs to be a common thread in the design so we can reuse elements in, for example, the email templates, the work order or receipt we give to our customers (we may contact the winner of the contest to design these for us as well!).

The name 'Handset Haven' is chosen. Rehab (short for rehabilitate) has a bold and playful tone to it and the design needs to reflect the name. So we're looking for a somewhat playful and cheeky design. Definitely not too serious and definitely modern. We already got a logo that we love and that fit's this description (see attached design documents for the logo). It's bold, powerful and fun. Our web design needs to reflect this as well and has to fit in with our logo.
We would really like it if the design somehow incorporates elements that highlight our unique selling points (repairs on location, we come to you etc.). We would really like some form of story telling in the design. Think clumsy people breaking their phones. Teenagers in tears because they have no access to their friends. People nowadays have the need to always be 'connected'. What happens when your phone is broken or malfunctioning? We're handling tech, we are nerds and a little bit weird, but we're professionals and here to help you with your problem. The sentiment Byte Brigade tries to communicate is something we really like. We're looking for fresh idea's, anything goes!

In an overview all Unique Selling Points of the Handset haven service:
- Professional service on location. Don’t ship to us we will come to you!
- Clear pricing upfront. No hidden cost.
- Next business-day repair.
- Backed by a professional call center open 12 hours a day and open on a Saturday as well
- Backed by a professional repair center with more then 12 years of experience
- Repair is done by certified engineers
- 1 year warranty on the repair

The process:
The main function of our website will be for customers to make a repair request. A customer will visit our website and can make a repair request immediately by going through a 'request-order-flow'. In this flow he or she will need to fill in some forms and can select wich type/model/brand of mobile device he or she has and what parts need to be repaired. After a request is placed we will call the customer back (within an hour) for a short intake and to set a date/time and location. Our engineer will meet the customer at the specified location and will repair the device onsite in one of our mobile repair centers, which is a specialized van equipped with all the tools needed for device restorations.
So in short the steps are:
- Choose your device and repair job
- Place the order
- Get a callback within the hour
- Set date and location
- We will come to you.

Website functionality:
Our website is our main form of communication. So the sentiment we want to communicate needs be reflected in the design. We need a main/front page designed (preferably a long scrolling page design) containing:
1. Customers will be able to request a repair job directly on our website. So there will need to be a prominent button/link at the top of our main page that will bring the customer to this 'request-order-flow'. This is the main flow which needs to be full focus on the front page. All other items are secondary.
2. The general information of who we are and what we do, and why the customer should choose us. Preferably in short bullet-point type keywords/sentences with icons or other visual cues. See our unique selling points to get an idea of the information that will be displayed here.
3. There needs to be a section that will explain the process (see above) of a repair request step-by- step, again in brief short key sentences and with (custom) icons.
4. There needs to be a section that explains to the customer he/she can always contact us if they are not sure what the problem is with their device, and for this reason are not sure what repair request they should order.
5. We want to implement some functionality that display customer ratings or customer reviews. So there needs to be room for some kind of widget of plugin we're going to implement which shows these reviews.
6. A 'For business section' where we will explain all the options we provide for corporate clients.
7. Social media links.
8. There needs to be a menu with buttons that leads to the all sections described in the previous points.

For now, we need a design for our front page. In the second phase, when we have picked our winner, we may ask the winner to design the page(s) for our request workflow as well.

EDIT:
Finally, we have a very specific order in mind for the different segments of our website. We would like you to add some more segments that were not in our original brief as well:

1. Top header with order/request button. (should instantly make clear our main USP, we do repairs on location)
2. Our process
3. Our unique selling points / why choose us
4. The kind of repairs we do (broken screens, broken batteries, water damage, broken camera's, no sound etc.)
5. A 'meet our team' section, where we introduce some of our engineers
6. A 'contact us for any questions' section/
7. Testimonials/user reviews
8. A section where we show key performance indicators
9. 'For businesses' sections
10.'Subscribe for newsletter' field
11. Social media buttons

Industry/Entity Type

It Service

Number of Pages Required

1 page

Font styles to use
Sans Serif

Requirements
Must have
• a main/front page, design only
• custom icons/images for banners, adverts online and in print (high res)
Nice to have
• Storytelling in our design.
• Design that fits with our brand new logo.
• Elements like icons to have a flat design.
• Keep in mind that the website will need to be responsive when designing! (Ideally provide an example of the mobile design as well)
• Create a fun and trustworthy feeling.

```html
<!DOCTYPE html>
<html lang="en">
<head>
<meta charset="utf-8">
<title>Handset Haven – We will come to you</title>
<link rel="stylesheet" href="https://fonts.googleapis.com/css2?family=Nunito+Sans:wght@400;600;700;800&family=Open+Sans:wght@400;600;700&display=swap">
<style>
:root{
  --orange:#e8652e;
  --orange-dark:#d9561f;
  --nav:#5a78a6;
  --ink:#222428;
  --text:#555a60;
  --muted:#8a8f96;
  --line:#d9dbdf;
  --icon-blue:#4e6a9a;
  --band:#eef1f8;
  --white:#ffffff;
}
*{box-sizing:border-box;margin:0;padding:0}
html,body{width:1200px;height:2769px;overflow:hidden;background:var(--white)}
body{font-family:"Open Sans",Arial,sans-serif;color:var(--text);position:relative}
a{color:inherit;text-decoration:none}

/* Header */
.site-header{position:absolute;left:0;top:0;width:1200px;height:111px}
.brand{position:absolute;left:98px;top:18px;display:flex;align-items:center;gap:14px}
.brand-dot{width:62px;height:62px;border-radius:50%;background:var(--orange);flex:none}
.brand-text{display:flex;flex-direction:column}
.brand-name{font-family:"Nunito Sans",sans-serif;font-weight:800;font-size:27px;line-height:26px;color:#3a3d42}
.brand-tag{margin-top:5px;font-family:"Nunito Sans",sans-serif;font-size:11px;line-height:13px;font-weight:800;color:#3a3d42;white-space:nowrap}
.util-links{position:absolute;right:98px;top:19px;display:flex;font-size:12px;color:#555}
.util-links span{display:flex;align-items:center;gap:5px}
.util-links .sep{margin:0 9px;color:#999}
.util-links svg{width:10px;height:10px;fill:var(--orange)}
.call{position:absolute;left:582px;top:57px;display:flex;align-items:center;gap:12px;font-size:14px;color:#333}
.call-ring{width:32px;height:32px;border:1.5px solid #bbb;border-radius:50%;display:flex;align-items:center;justify-content:center}
.call b{font-size:20px;font-weight:700;color:#222;margin-left:4px}
.cart{position:absolute;left:884px;top:56px;display:flex;align-items:center;gap:12px;font-size:13px}
.cart b{color:#222;font-weight:700;font-size:14px}
.cart small{color:#999;font-size:11px}

/* Nav */
.main-nav{position:absolute;left:0;top:111px;width:1200px;height:42px;background:var(--nav)}
.main-nav ul{list-style:none;position:absolute;left:98px;top:0;height:42px;display:flex;align-items:center}
.main-nav li{font-family:"Nunito Sans",sans-serif;font-weight:700;font-size:16px;color:var(--white);margin-right:33px}
.main-nav li.active{color:#ff9a6c}
.search{position:absolute;left:738px;top:5px;width:362px;height:33px;background:var(--white);border-radius:17px;font-size:13px;color:#888;padding:8px 20px}
.search svg{position:absolute;right:14px;top:9px}

/* Hero */
.hero{position:absolute;left:0;top:153px;width:1200px;height:441px;background:linear-gradient(90deg,#7d7d7d 0%,#9a9a9a 35%,#8a8a8a 60%,#6f6f6f 100%)}
.hero-photo{position:absolute;left:0;top:0;width:1200px;height:441px;background:radial-gradient(ellipse at 26% 40%,#c9c9c9 0%,rgba(160,160,160,0) 45%),linear-gradient(180deg,rgba(0,0,0,0) 70%,rgba(255,255,255,.35) 100%)}
.hero-arrow{position:absolute;top:194px;width:45px;height:52px;border:1px solid rgba(255,255,255,.6);background:rgba(0,0,0,.15);display:flex;align-items:center;justify-content:center}
.hero-arrow.prev{left:18px}
.hero-arrow.next{left:1137px}
.hero-kicker{position:absolute;left:526px;top:130px;font-family:"Nunito Sans",sans-serif;font-size:31px;color:var(--white);font-weight:400}
.hero-title{position:absolute;left:526px;top:176px;font-family:"Nunito Sans",sans-serif;font-size:46px;line-height:56px;font-weight:800;color:var(--white);white-space:nowrap}
.locator{position:absolute;left:528px;top:255px;width:473px;height:46px;display:flex}
.locator-field{flex:1;background:var(--white);display:flex;align-items:center;padding:0 16px;font-size:14px;color:#777;gap:12px;position:relative}
.locator-field .caret{position:absolute;right:16px}
.locator-go{width:56px;background:var(--orange);color:var(--white);font-weight:700;font-size:15px;display:flex;align-items:center;justify-content:center}

/* Welcome */
.welcome{position:absolute;left:98px;top:594px;width:1004px;height:412px;border-bottom:1px solid var(--line)}
.welcome h1{position:absolute;left:0;top:62px;font-family:"Nunito Sans",sans-serif;font-size:30px;font-weight:800;color:var(--ink)}
.welcome p{position:absolute;left:0;width:480px;font-size:12.5px;line-height:26px;color:#555}
.welcome .p1{top:120px}
.welcome .p2{top:198px}
.read-more{position:absolute;left:0;top:335px;width:136px;height:37px;border:1.5px solid #c8c8c8;border-radius:19px;color:var(--orange);font-size:12px;font-weight:700;display:flex;align-items:center;justify-content:center}
.video{position:absolute;left:530px;top:78px;width:474px;height:288px;border:1px solid #ccc;padding:4px;background:var(--white)}
.video-still{width:100%;height:100%;background:linear-gradient(135deg,#d8dde6 0%,#b9c4d3 40%,#6f7784 70%,#e4e6ea 100%);position:relative}
.play{position:absolute;left:50%;top:50%;width:64px;height:64px;margin:-32px 0 0 -32px;border-radius:50%;background:rgba(30,30,30,.8);display:flex;align-items:center;justify-content:center}

/* Why */
.why{position:absolute;left:0;top:1006px;width:1200px;height:523px}
.section-title{font-family:"Nunito Sans",sans-serif;font-size:28px;font-weight:800;color:var(--ink);text-align:center}
.why .section-title{position:absolute;left:0;width:1200px;top:48px}
.usp{position:absolute;width:320px;text-align:center;font-family:"Nunito Sans",sans-serif;font-size:17px;line-height:27px;color:#2a2c30;font-weight:600}
.usp svg{display:block;margin:0 auto 18px;height:56px}

/* How it works */
.how{position:absolute;left:0;top:1529px;width:1200px;height:387px;background:var(--band)}
.how .section-title{position:absolute;left:0;width:1200px;top:52px}
.step{position:absolute;top:148px;width:200px;text-align:center;font-family:"Nunito Sans",sans-serif;font-weight:600;font-size:16px;line-height:26px;color:#2a2c30}
.step svg{display:block;margin:0 auto 22px;height:96px}
.step-arrow{position:absolute;top:214px}

/* Support */
.support{position:absolute;left:0;top:1916px;width:1200px;height:488px}
.support-photo{position:absolute;left:0;top:0;width:600px;height:488px;background:linear-gradient(180deg,#eef0f2 0%,#d7dbe0 45%,#6a7fa8 70%,#3a3f48 100%)}
.support-panel{position:absolute;left:600px;top:0;width:600px;height:488px;background:linear-gradient(180deg,var(--orange) 0%,var(--orange-dark) 100%);color:var(--white)}
.support-panel h2{position:absolute;left:61px;top:54px;font-family:"Nunito Sans",sans-serif;font-size:30px;line-height:40px;font-weight:800}
.support-panel p{position:absolute;left:61px;top:148px;width:460px;font-size:14px;line-height:26px;color:#ffe4d6}
.perk{position:absolute;left:61px;display:flex;align-items:center;gap:30px;font-family:"Nunito Sans",sans-serif;font-size:21px;line-height:27px;font-weight:600}
.perk-ring{width:89px;height:89px;border:2px solid var(--white);border-radius:50%;display:flex;align-items:center;justify-content:center}

/* Footer */
.site-footer{position:absolute;left:0;top:2404px;width:1200px;height:365px}
.foot-col{position:absolute;top:68px;height:200px}
.foot-col h3{font-family:"Nunito Sans",sans-serif;font-size:19px;font-weight:700;color:var(--ink);margin-bottom:12px}
.foot-col li{list-style:none;font-size:12px;line-height:27.5px;color:#555}
.foot-divider{position:absolute;top:68px;width:1px;height:186px;background:var(--line)}
.foot-col .note{font-size:12px;color:#555;margin-bottom:14px}
.subscribe{display:flex;width:325px;height:36px}
.subscribe span{flex:1;border:1px solid #ccc;font-size:12px;color:#777;padding:10px 12px}
.subscribe b{width:94px;background:var(--orange);color:var(--white);font-size:12px;font-weight:700;display:flex;align-items:center;justify-content:center}
.stay{font-family:"Nunito Sans",sans-serif;font-size:19px;font-weight:700;color:var(--ink);margin:20px 0 12px}
.socials{display:flex;gap:11px}
.socials i{width:33px;height:33px;border-radius:50%;display:block}
.copyright{position:absolute;left:98px;top:295px;width:1004px;border-top:1px solid var(--line);padding-top:22px;text-align:center;font-size:11.5px;color:#555}
</style>
</head>
<body>

<header class="site-header">
  <div class="brand">
    <span class="brand-dot"></span>
    <span class="brand-text">
      <span class="brand-name">HANDSET<br>HAVEN</span>
      <span class="brand-tag">We will come to you!</span>
    </span>
  </div>

  <nav class="util-links">
    <span><svg viewBox="0 0 10 10"><path d="M5 0a3.5 3.5 0 0 0-3.5 3.5C1.5 6 5 10 5 10s3.5-4 3.5-6.5A3.5 3.5 0 0 0 5 0z"/></svg>Store Locator</span><span class="sep">|</span>
    <span><svg viewBox="0 0 10 10"><rect x="1" y="4" width="8" height="6"/><rect x="0" y="2" width="10" height="2.5"/></svg>Gift Cards</span><span class="sep">|</span>
    <span><svg viewBox="0 0 10 10"><path d="M5 9L1 5a2.3 2.3 0 0 1 4-3 2.3 2.3 0 0 1 4 3z"/></svg>Wishlist</span><span class="sep">|</span>
    <span><svg viewBox="0 0 10 10"><circle cx="5" cy="3" r="2.5"/><path d="M0 10c0-3 2-4.5 5-4.5S10 7 10 10z"/></svg>My Account</span><span class="sep">|</span>
    <span><svg viewBox="0 0 10 10"><rect x="1" y="4.5" width="8" height="5.5"/><path d="M2.5 4.5V3a2.5 2.5 0 0 1 5 0v1.5" fill="none" stroke="#e8652e" stroke-width="1.4"/></svg>Login</span>
  </nav>

  <div class="call">
    <span class="call-ring"><svg width="14" height="14" viewBox="0 0 14 14"><path d="M3 1l2.2 2.6-1.3 1.6a8 8 0 0 0 4.9 4.9l1.6-1.3L13 11l-1.6 2C6 13 1 8 1 2.6z" fill="#e8652e"/></svg></span>
    <span>Call us on: <b>1 800 555 0142</b></span>
  </div>

  <div class="cart">
    <svg width="30" height="26" viewBox="0 0 30 26"><path d="M1 2h5l4 15h15l3-10H8" fill="none" stroke="#e8652e" stroke-width="2.4" stroke-linejoin="round"/><circle cx="12" cy="22" r="2.2" fill="#e8652e"/><circle cx="23" cy="22" r="2.2" fill="#e8652e"/></svg>
    <span><b>My Cart</b> &nbsp;<small>0 item(s) | $ 0.00 &nbsp;▾</small></span>
  </div>
</header>

<nav class="main-nav">
  <ul>
    <li class="active">Home</li>
    <li>About Us</li>
    <li>Services</li>
    <li>Products</li>
    <li>Brands</li>
    <li>Deals</li>
    <li>Contact</li>
  </ul>
  <div class="search">Search
    <svg width="15" height="15" viewBox="0 0 15 15"><circle cx="6" cy="6" r="4.8" fill="none" stroke="#888" stroke-width="1.6"/><path d="M9.5 9.5l4 4" stroke="#888" stroke-width="1.8"/></svg>
  </div>
</nav>

<section class="hero">
  <div class="hero-photo" role="img" aria-label="Smartphone with a shattered screen standing on a grey surface"></div>
  <span class="hero-arrow prev"><svg width="14" height="22" viewBox="0 0 14 22"><path d="M12 2L3 11l9 9" fill="none" stroke="#fff" stroke-width="2"/></svg></span>
  <span class="hero-arrow next"><svg width="14" height="22" viewBox="0 0 14 22"><path d="M2 2l9 9-9 9" fill="none" stroke="#fff" stroke-width="2"/></svg></span>
  <div class="hero-kicker">Handset Haven</div>
  <div class="hero-title">WE WILL COME TO YOU</div>
  <div class="locator">
    <div class="locator-field">
      <svg width="12" height="16" viewBox="0 0 12 16"><path d="M6 0a5.5 5.5 0 0 0-5.5 5.5C.5 9.5 6 16 6 16s5.5-6.5 5.5-10.5A5.5 5.5 0 0 0 6 0zm0 8a2.5 2.5 0 1 1 0-5 2.5 2.5 0 0 1 0 5z" fill="#777"/></svg>
      Choose Your Location
      <svg class="caret" width="12" height="8" viewBox="0 0 12 8"><path d="M1 1l5 5 5-5" fill="none" stroke="#777" stroke-width="1.6"/></svg>
    </div>
    <div class="locator-go">GO</div>
  </div>
</section>

<section class="welcome">
  <h1>WELCOME TO HANDSET HAVEN</h1>
  <p class="p1">Our company is based in Rotterdam, the Netherlands. We provide different services for all kinds of electronic devices.</p>
  <p class="p2">The kind of services we provide are, among other things, installations of hardware and software and the repair of broken or malfunctioning devices. We are starting a new service that offers mobile device repairs on location, be it at the home of our customers, their office, or any other place.</p>
  <a class="read-more">READ MORE &gt;&gt;</a>
  <div class="video">
    <div class="video-still" role="img" aria-label="Video still of gloved hands repairing a smartphone with a screwdriver">
      <span class="play"><svg width="22" height="24" viewBox="0 0 22 24"><path d="M3 2l17 10L3 22z" fill="#fff"/></svg></span>
    </div>
  </div>
</section>

<section class="why">
  <h2 class="section-title">WHY REAPIR AT HANDSET HAVEN</h2>

  <div class="usp" style="left:87px;top:136px">
    <svg viewBox="0 0 40 56" width="40"><path d="M20 2A17 17 0 0 0 3 19c0 13 17 35 17 35s17-22 17-35A17 17 0 0 0 20 2zm0 24a7 7 0 1 1 0-14 7 7 0 0 1 0 14z" fill="#e8652e"/></svg>
    Professional service on location. Don't ship to us we will come to you!
  </div>
  <div class="usp" style="left:440px;top:136px">
    <svg viewBox="0 0 72 56" width="72"><rect x="2" y="8" width="68" height="40" fill="none" stroke="#e8652e" stroke-width="4"/><rect x="9" y="15" width="54" height="26" fill="#e8652e"/><circle cx="36" cy="28" r="10" fill="#fff"/><path d="M34 23h3v11" stroke="#e8652e" stroke-width="2.6" fill="none"/></svg>
    Clear pricing upfront.<br>No hidden cost.
  </div>
  <div class="usp" style="left:791px;top:136px">
    <svg viewBox="0 0 56 56" width="56"><path d="M40 3a14 14 0 0 0-13 19L4 45a5 5 0 0 0 7 7l23-23A14 14 0 0 0 53 16l-8 8-9-4-3-9 8-8z" fill="#e8652e"/></svg>
    Next business-day<br>repair
  </div>
  <div class="usp" style="left:87px;top:322px">
    <svg viewBox="0 0 56 56" width="56"><rect x="2" y="24" width="12" height="30" fill="#e8652e"/><path d="M18 26l12-20c5 0 7 4 6 8l-2 9h15c4 0 6 4 5 7l-5 19c-1 3-3 5-6 5H18z" fill="#e8652e"/></svg>
    1 year warranty on the<br>repair
  </div>
  <div class="usp" style="left:440px;top:322px">
    <svg viewBox="0 0 70 56" width="70"><circle cx="35" cy="10" r="9" fill="#e8652e"/><circle cx="14" cy="20" r="7" fill="#e8652e"/><circle cx="56" cy="20" r="7" fill="#e8652e"/><path d="M20 54V34a15 15 0 0 1 30 0v20z" fill="#e8652e"/><path d="M2 54V40a12 12 0 0 1 18-8v22zM68 54V40a12 12 0 0 0-18-8v22z" fill="#e8652e"/></svg>
    Repair is done by certified<br>engineers
  </div>
  <div class="usp" style="left:791px;top:322px">
    <svg viewBox="0 0 60 56" width="60"><path d="M30 2l8 18 20 2-15 13 4 20-17-10-17 10 4-20L2 22l20-2z" fill="#e8652e"/></svg>
    Professional repair center with more then 12 years of experience
  </div>
</section>

<section class="how">
  <h2 class="section-title">HOW IT WORKS</h2>

  <div class="step" style="left:68px">
    <svg viewBox="0 0 60 96" width="60"><rect x="12" y="2" width="44" height="82" rx="6" fill="none" stroke="#4e6a9a" stroke-width="4"/><rect x="4" y="10" width="44" height="84" rx="6" fill="#eef1f8" stroke="#4e6a9a" stroke-width="4"/><rect x="10" y="20" width="32" height="60" fill="none" stroke="#4e6a9a" stroke-width="2"/></svg>
    Choose your device<br>and repair job
  </div>
  <div class="step" style="left:291px">
    <svg viewBox="0 0 64 96" width="64"><rect x="4" y="4" width="48" height="88" rx="6" fill="none" stroke="#4e6a9a" stroke-width="4"/><path d="M22 44h36l-4 18H26z" fill="#eef1f8" stroke="#4e6a9a" stroke-width="3"/><path d="M30 44l6-10 6 10" fill="none" stroke="#4e6a9a" stroke-width="3"/><path d="M32 48v10M40 48v10M48 48v10" stroke="#4e6a9a" stroke-width="2.4"/><circle cx="28" cy="82" r="3" fill="#4e6a9a"/></svg>
    Place the<br>order
  </div>
  <div class="step" style="left:511px">
    <svg viewBox="0 0 80 96" width="80"><rect x="8" y="22" width="42" height="72" rx="6" fill="none" stroke="#4e6a9a" stroke-width="4"/><path d="M8 80h42" stroke="#4e6a9a" stroke-width="3"/><path d="M48 14a16 16 0 0 1 16 16M50 4a26 26 0 0 1 26 26M46 22a8 8 0 0 1 8 8" fill="none" stroke="#4e6a9a" stroke-width="4"/></svg>
    Get a callback within<br>the hour
  </div>
  <div class="step" style="left:731px">
    <svg viewBox="0 0 60 96" width="60"><rect x="4" y="4" width="52" height="88" rx="6" fill="#4e6a9a"/><rect x="10" y="14" width="40" height="62" fill="#eef1f8"/><path d="M30 24a10 10 0 0 0-10 10c0 8 10 20 10 20s10-12 10-20a10 10 0 0 0-10-10zm0 14a4 4 0 1 1 0-8 4 4 0 0 1 0 8z" fill="#4e6a9a"/><circle cx="30" cy="84" r="3.5" fill="#eef1f8"/></svg>
    Set date and<br>location
  </div>
  <div class="step" style="left:952px">
    <svg viewBox="0 0 86 96" width="86"><path d="M43 8L4 44h10v48h58V44h10z" fill="#4e6a9a"/><path d="M14 44L43 18l29 26" fill="none" stroke="#eef1f8" stroke-width="3"/><rect x="34" y="60" width="18" height="32" fill="#eef1f8"/></svg>
    We will come<br>to you
  </div>

  <svg class="step-arrow" style="left:228px" width="100" height="14" viewBox="0 0 100 14"><path d="M0 7h96" stroke="#e8652e" stroke-width="2.4" stroke-dasharray="7 6"/><path d="M56 1l7 6-7 6" fill="none" stroke="#e8652e" stroke-width="2.6"/></svg>
  <svg class="step-arrow" style="left:451px" width="100" height="14" viewBox="0 0 100 14"><path d="M0 7h96" stroke="#e8652e" stroke-width="2.4" stroke-dasharray="7 6"/><path d="M56 1l7 6-7 6" fill="none" stroke="#e8652e" stroke-width="2.6"/></svg>
  <svg class="step-arrow" style="left:671px" width="100" height="14" viewBox="0 0 100 14"><path d="M0 7h96" stroke="#e8652e" stroke-width="2.4" stroke-dasharray="7 6"/><path d="M56 1l7 6-7 6" fill="none" stroke="#e8652e" stroke-width="2.6"/></svg>
  <svg class="step-arrow" style="left:891px" width="100" height="14" viewBox="0 0 100 14"><path d="M0 7h96" stroke="#e8652e" stroke-width="2.4" stroke-dasharray="7 6"/><path d="M56 1l7 6-7 6" fill="none" stroke="#e8652e" stroke-width="2.6"/></svg>
</section>

<section class="support">
  <div class="support-photo" role="img" aria-label="Two repair engineers in blue work uniforms with toolboxes standing beside a white service van"></div>
  <div class="support-panel">
    <h2>SAVE $100 ON HANDSET HAVEN<br>24/7 SUPPORT</h2>
    <p>Backed by a professional call center open 12 hours a day and open on a Saturday as well</p>
    <div class="perk" style="top:225px">
      <span class="perk-ring"><svg width="40" height="30" viewBox="0 0 40 30"><rect x="2" y="2" width="36" height="26" rx="3" fill="none" stroke="#fff" stroke-width="2.6"/><path d="M2 10h36" stroke="#fff" stroke-width="4"/><path d="M8 20h10" stroke="#fff" stroke-width="2.6"/></svg></span>
      <span>Get a Gift card for<br>your device</span>
    </div>
    <div class="perk" style="top:340px">
      <span class="perk-ring"><svg width="42" height="40" viewBox="0 0 42 40"><circle cx="15" cy="24" r="9" fill="none" stroke="#fff" stroke-width="6" stroke-dasharray="4 3"/><circle cx="15" cy="24" r="4" fill="#fff"/><circle cx="32" cy="10" r="6" fill="none" stroke="#fff" stroke-width="4" stroke-dasharray="3 2.4"/></svg></span>
      <span>Expert Service.<br>Unbeatable Price</span>
    </div>
  </div>
</section>

<footer class="site-footer">
  <div class="foot-col" style="left:98px">
    <h3>Information</h3>
    <ul><li>About Us</li><li>Careers</li><li>Privacy &amp; Security</li><li>Site Map</li><li>Terms of Use</li><li>Blog</li></ul>
  </div>
  <span class="foot-divider" style="left:280px"></span>
  <div class="foot-col" style="left:303px">
    <h3>Help &amp; support</h3>
    <ul><li>Login</li><li>New Customers</li><li>Products</li><li>Phone Repair</li><li>Frequently Asked Questions</li><li>How to Order</li></ul>
  </div>
  <span class="foot-divider" style="left:508px"></span>
  <div class="foot-col" style="left:550px">
    <h3>My Account</h3>
    <ul><li>Delivery Information</li><li>My Account</li><li>Order Tracking</li><li>Reminder Service</li><li>Shipping, Returns &amp; Fees</li></ul>
  </div>
  <span class="foot-divider" style="left:731px"></span>
  <div class="foot-col" style="left:777px">
    <h3>Email Subscription</h3>
    <div class="note">Register your email address to get information about us</div>
    <div class="subscribe"><span>Email Address</span><b>SUBSCRIBE</b></div>
    <div class="stay">Stay Connected</div>
    <div class="socials" aria-label="Social media links">
      <i style="background:#3b5b9b"></i><i style="background:#3aa8e0"></i><i style="background:#d6493a"></i><i style="background:#4d6b8f"></i><i style="background:#3ab0d2"></i><i style="background:#d12a2a"></i><i style="background:#c8232c"></i>
    </div>
  </div>
  <div class="copyright">Copyrights © 2017, Handset Haven. All Rights Reserved &nbsp;| &nbsp;Privacy Policy | Terms of Use | Feedback</div>
</footer>

</body>
</html>
```